The Velvet Rig

need a business card for a dj and sound equipment hire(rentals) business based in Melbourne. i have attached a current card get an idea. card needs to be unique professional looking.

ps.this card is not for a DJ. it's a rental business of dj equipment and pa systems.

Industry/Entity Type

Business

Font styles to use
Sans Serif
Script

Requirements
Must have
• Business Name: THE VELVET RIG
Contact Person: KIERAN MALLORY
Mobile: 047 VELVET 91
Email: KIERAN@THEVELVETRIG.COM.AU
Website: WWW.THEVELVETRIG.COM.AU
Pixelwall: WWW.PIXELWALL.CM/THEVELVETRIG.COM.AU

```html
<!DOCTYPE html>
<html lang="en">
<head>
<meta charset="utf-8">
<title>The Velvet Rig — Business Card</title>
<link href="https://fonts.googleapis.com/css2?family=Great+Vibes&family=Libre+Baskerville&display=swap" rel="stylesheet">
<style>
  :root {
    --stage: #2b3750;
    --card: #050506;
    --teal: #3aa69b;
    --teal-glow: #39c9e0;
    --deck-deep: #04060d;
    --deck-blue: #16305c;
    --deck-cyan: #3f8fd6;
    --matrix-light: #8d8d8d;
    --matrix-dark: #1a1a1a;
  }
  * { margin: 0; padding: 0; box-sizing: border-box; }
  html, body {
    width: 1200px; height: 1000px; overflow: hidden;
    background: var(--stage);
  }
  .stage {
    width: 1200px; height: 1000px;
    display: flex; align-items: center; justify-content: center;
  }
  .card {
    position: relative;
    width: 1020px; height: 580px;
    background: var(--card);
    overflow: hidden;
    box-shadow: 0 12px 40px rgba(0,0,0,.45);
  }
  .deck-photo {
    position: absolute; left: 0; right: 0; top: 230px; bottom: 0;
    background:
      radial-gradient(ellipse at 70% 60%, rgba(63,143,214,.55), transparent 60%),
      radial-gradient(ellipse at 8% 85%, rgba(220,80,30,.35), transparent 30%),
      linear-gradient(180deg, var(--card) 0%, var(--deck-deep) 18%, var(--deck-blue) 65%, var(--deck-deep) 100%);
  }
  .light-matrix {
    position: absolute; right: 0; top: 0; width: 420px; height: 300px;
    background:
      radial-gradient(ellipse at 60% 30%, rgba(200,200,200,.55), transparent 65%),
      linear-gradient(180deg, var(--matrix-light) 0%, var(--matrix-dark) 85%, transparent 100%);
    opacity: .55;
    -webkit-mask-image: linear-gradient(90deg, transparent 0%, #000 25%);
            mask-image: linear-gradient(90deg, transparent 0%, #000 25%);
  }
  .brand-mark {
    position: absolute; left: 48px; top: 36px;
    width: 190px; height: 190px; border-radius: 50%;
    background: #1c1c1f;
    box-shadow: 0 0 28px rgba(57,201,224,.55);
  }
  .business-name {
    position: absolute; left: 262px; top: 18px;
    font-family: "Great Vibes", cursive;
    font-size: 88px; line-height: 1; color: var(--teal);
    white-space: nowrap;
  }
  .contact-name {
    position: absolute; left: 268px; top: 112px;
    font-family: "Libre Baskerville", serif;
    font-size: 40px; color: var(--teal); white-space: nowrap;
  }
  .contact {
    position: absolute; top: 232px;
    font-family: "Libre Baskerville", serif;
    font-size: 17px; line-height: 1.45; color: var(--teal);
    white-space: nowrap; text-transform: uppercase;
  }
  .contact-left { left: 218px; }
  .contact-right { left: 540px; top: 208px; }
</style>
</head>
<body>
<main class="stage">
  <section class="card">
    <div class="deck-photo" role="img" aria-label="Close-up photograph of a DJ mixer with glowing blue knobs and faders"></div>
    <div class="light-matrix" role="img" aria-label="Dot-matrix LED lighting pattern"></div>
    <div class="brand-mark"></div>
    <h1 class="business-name">The Velvet Rig</h1>
    <p class="contact-name">Kieran Mallory</p>
    <div class="contact contact-left">
      <p>047 VELVET 91</p>
      <p>WWW.THEVELVETRIG.COM.AU</p>
    </div>
    <div class="contact contact-right">
      <p>KIERAN@THEVELVETRIG.COM.AU</p>
      <p>WWW.PIXELWALL.CM/THEVELVETRIG.COM.AU</p>
    </div>
  </section>
</main>
</body>
</html>
```